MRT Property - Business Cards

Looking for a business card & general letterhead, signage etc design for our new logo.

Colours:
000a20
0056a2
00b5ef
0088ce
68cef2

Fonts:
Poppins
Karla

Please keep look and feel of new brand - example in the zip package I sent.

```html
<!DOCTYPE html>
<html lang="en">
<head>
<meta charset="utf-8">
<title>MRT Property – Business Cards</title>
<link href="https://fonts.googleapis.com/css2?family=Poppins:wght@400;500;600;700&display=swap" rel="stylesheet">
<style>
  :root {
    --ink: #000a20;
    --navy: #0056a2;
    --cyan: #00b5ef;
    --azure: #0088ce;
    --sky: #68cef2;
    --paper: #ffffff;
    --stage: #2e2e30;
  }
  * { margin: 0; padding: 0; box-sizing: border-box; }
  html, body {
    width: 1200px; height: 689px; overflow: hidden;
    background: var(--stage);
    font-family: "Poppins", sans-serif;
  }
  .sheet {
    position: relative; width: 1200px; height: 689px;
    display: flex; align-items: center; justify-content: center; gap: 40px;
  }
  .card {
    position: relative; width: 520px; height: 297px;
    border-radius: 18px; overflow: hidden;
  }
  .card--front {
    background: var(--azure);
    display: flex; align-items: center; justify-content: center;
  }
  .brand {
    display: flex; align-items: center; gap: 14px;
    font-weight: 700; letter-spacing: 0.5px; white-space: nowrap;
  }
  .brand__dot { border-radius: 50%; flex: none; }
  .card--front .brand { font-size: 46px; color: var(--sky); }
  .card--front .brand__dot { width: 40px; height: 40px; background: var(--navy); }

  .card--back { display: flex; background: var(--paper); }
  .back__logo {
    width: 300px; display: flex; align-items: center; justify-content: center;
    padding-top: 40px;
  }
  .back__logo .brand { font-size: 31px; color: var(--navy); gap: 10px; }
  .back__logo .brand__dot { width: 28px; height: 28px; background: var(--cyan); }
  .back__rule { width: 5px; background: var(--cyan); }
  .back__panel {
    flex: 1; background: var(--navy); color: var(--paper);
    padding: 34px 24px 0 26px;
  }
  .person__name { font-size: 21px; font-weight: 700; line-height: 1.1; }
  .person__role { font-size: 12px; font-weight: 400; margin-top: 2px; }
  .address { font-size: 12px; line-height: 1.45; margin-top: 40px; }
  .contacts { list-style: none; margin-top: 10px; font-size: 12px; line-height: 1.45; }
  .contacts li { display: flex; align-items: center; gap: 8px; }
  .contacts svg { width: 11px; height: 11px; flex: none; fill: var(--paper); }
</style>
</head>
<body>
<main class="sheet">
  <section class="card card--front" aria-label="Card front">
    <div class="brand"><span class="brand__dot"></span>MRT Property</div>
  </section>

  <section class="card card--back" aria-label="Card back">
    <div class="back__logo">
      <div class="brand"><span class="brand__dot"></span>MRT Property</div>
    </div>
    <div class="back__rule"></div>
    <div class="back__panel">
      <p class="person__name">Daniel Reeves</p>
      <p class="person__role">President</p>
      <p class="address">4120 Harbour View Road<br>Halden, Canada 52810</p>
      <ul class="contacts">
        <li><svg viewBox="0 0 24 24"><path d="M6.6 10.8a15 15 0 0 0 6.6 6.6l2.2-2.2a1 1 0 0 1 1-.25 11 11 0 0 0 3.6.6 1 1 0 0 1 1 1V20a1 1 0 0 1-1 1A17 17 0 0 1 3 4a1 1 0 0 1 1-1h3.5a1 1 0 0 1 1 1 11 11 0 0 0 .6 3.6 1 1 0 0 1-.25 1z"/></svg>555-210-4812</li>
        <li><svg viewBox="0 0 24 24"><path d="M7 1h10a2 2 0 0 1 2 2v18a2 2 0 0 1-2 2H7a2 2 0 0 1-2-2V3a2 2 0 0 1 2-2zm0 3v14h10V4zm5 15.5a1 1 0 1 0 0 2 1 1 0 0 0 0-2z"/></svg>555-384-9027</li>
        <li><svg viewBox="0 0 24 24"><path d="M2 5h20v14H2zm2 2v.5l8 5 8-5V7zm0 2.8V17h16V9.8l-8 5z"/></svg>info@mrtproperty.com</li>
        <li><svg viewBox="0 0 24 24"><path d="M12 2a10 10 0 1 0 0 20 10 10 0 0 0 0-20zm0 2c1.2 1.4 2 3.6 2.2 6H9.8C10 7.6 10.8 5.4 12 4zM4.1 13h3.7c.1 2.1.7 4.1 1.6 5.6A8 8 0 0 1 4.1 13zm0-2a8 8 0 0 1 5.3-5.6c-.9 1.5-1.5 3.5-1.6 5.6zm7.9 9c-1.2-1.4-2-3.6-2.2-7h4.4c-.2 3.4-1 5.6-2.2 7zm2.6-1.4c.9-1.5 1.5-3.5 1.6-5.6h3.7a8 8 0 0 1-5.3 5.6zm1.6-7.6c-.1-2.1-.7-4.1-1.6-5.6a8 8 0 0 1 5.3 5.6z"/></svg>www.mrtproperty.com</li>
      </ul>
    </div>
  </section>
</main>
</body>
</html>
```